Business Card Design Project : Ridgeline Press

In preparation for market launch, Tamarind's Ridgeline Press require the development of a business card. Ridgeline Press is a Community online publishing web portal. We provide the the city of Whistler located in B.C. (Canada) business directories, News, Classified ads, News, Events and blogs etc.

The main focus of the brand is to help local businesses to corporate with their online advertisement and marketing. Meeting our clients face to face is a must (B2B).

Target Market(s)

The target market is B2B customers. Business Owners to Marketing, advertising Managers

Industry/Entity Type

Business

Requirements
Must have
• - The business card will be two sided.
the BACK side will have our logo which consist of (icon, url,slogan) submited. The logo will be middle and centred.

The FRONT side should have company details:

Company Legal Name: TAMARIND RIDGELINE MEDIA

Owen Farsk
Director of Sales & Marketing

www.tamarindridgeline.biz
owen@tamarindridgeline.biz

Phone: 604 317 8842
#2714 - 582 E. Halvern St.
Vancouver, B.C. V7K2R4 Canada
Nice to have
• - For the "FRONT" side of our business card. You can separate or re-arrange with our logo components (icon, logo,slogan). It does not have to be together.

Also our company legal name is rather long so arrange or organize the name in a way to make it shorter. Your experience and creativity will have to come in play.
Should not have
• should not have other colors beside logo color and black text (2 colors). Also nothing Three dimensional

```html
<!DOCTYPE html>
<html lang="en">
<head>
<meta charset="utf-8">
<title>Ridgeline Press – Business Card</title>
<link rel="stylesheet" href="https://fonts.googleapis.com/css2?family=Open+Sans:ital,wght@0,400;0,600;0,700;0,800;1,400&display=swap">
<style>
  :root {
    --brand-blue: #1f72bd;
    --brand-blue-light: #3d8fd6;
    --brand-blue-dark: #145a9a;
    --ink: #1a1a1a;
    --paper: #ffffff;
    --paper-shade: #eef0f2;
    --stage: #e4e6e8;
    --strip: #2b2b2b;
  }
  * { box-sizing: border-box; margin: 0; padding: 0; }
  html, body {
    width: 1200px; height: 944px; overflow: hidden;
    background: var(--stage);
    font-family: "Open Sans", Arial, sans-serif;
  }
  .canvas { position: relative; width: 1200px; height: 944px; }

  .card {
    position: absolute;
    width: 620px; height: 354px;
    border-radius: 26px;
    overflow: hidden;
  }

  /* Back side */
  .card--back {
    left: 60px; top: 90px;
    background: linear-gradient(160deg, var(--brand-blue-light) 0%, var(--brand-blue) 55%, var(--brand-blue-dark) 100%);
    color: var(--paper);
  }
  .card--back .brand-name {
    position: absolute; left: 0; right: 0; top: 78px;
    text-align: center;
    font-size: 48px; font-weight: 700; letter-spacing: 0.5px;
    color: var(--paper);
  }
  .card--back .brand-url {
    position: absolute; left: 0; right: 0; top: 168px;
    text-align: center;
    font-size: 37px; font-weight: 800;
    color: var(--ink);
  }
  .card--back .brand-slogan {
    position: absolute; left: 0; right: 0; top: 222px;
    text-align: center;
    font-size: 30px; font-weight: 400;
    color: var(--paper);
  }

  /* Front side */
  .card--front {
    left: 520px; top: 510px;
    background: linear-gradient(180deg, var(--paper) 0%, var(--paper-shade) 100%);
    color: var(--ink);
  }
  .card--front .brand-name {
    position: absolute; left: 0; right: 0; top: 34px;
    text-align: center;
    font-size: 40px; font-weight: 700;
    color: var(--brand-blue);
  }
  .card--front .brand-slogan {
    position: absolute; left: 0; right: 0; top: 96px;
    text-align: center;
    font-size: 19px;
  }
  .person { position: absolute; left: 44px; top: 142px; }
  .person__name { font-size: 22px; font-weight: 400; }
  .person__title { font-size: 15px; font-style: italic; color: var(--brand-blue); }

  .address {
    position: absolute; left: 44px; top: 206px;
    display: flex; gap: 8px;
    font-size: 16px; line-height: 22px;
  }
  .contacts {
    position: absolute; left: 360px; top: 202px;
    list-style: none; font-size: 16px; line-height: 25px;
  }
  .contacts li { display: flex; align-items: center; gap: 8px; }
  .icon { width: 16px; height: 16px; flex: none; fill: var(--brand-blue); }
  .address .icon { margin-top: 3px; }

  .front-band { position: absolute; left: 0; bottom: 0; width: 620px; height: 60px; }
</style>
</head>
<body>
<main class="canvas">

  <section class="card card--back" aria-label="Business card back">
    <div class="brand-name">Ridgeline Press</div>
    <div class="brand-url">www.tamarindridgeline.biz</div>
    <div class="brand-slogan">Your information gateway</div>
  </section>

  <section class="card card--front" aria-label="Business card front">
    <div class="brand-name">Ridgeline Press</div>
    <div class="brand-slogan">Your information gateway</div>

    <div class="person">
      <div class="person__name">Owen Farsk</div>
      <div class="person__title">Director of Sales &amp; Marketing</div>
    </div>

    <div class="address">
      <svg class="icon" viewBox="0 0 16 16" aria-hidden="true"><path d="M8 1 1 7.5h2V15h4v-4h2v4h4V7.5h2z"/></svg>
      <div>#2714 - 582 E. Halvern St.<br>Vancouver, B.C.V7K2R4 Canada</div>
    </div>

    <ul class="contacts">
      <li><svg class="icon" viewBox="0 0 16 16" aria-hidden="true"><path d="M4 1.5 6.3 4 5 6c.8 1.9 2.4 3.6 4.9 5l2-1.4 2.6 2.3-1.6 2.4C8 14.5 1.5 8 1.7 3z"/></svg>604 317 8842</li>
      <li><svg class="icon" viewBox="0 0 16 16" aria-hidden="true"><path d="M1 4h14v9H1z M1 4l7 5 7-5" fill="none" stroke="#1f72bd" stroke-width="1.6"/></svg>owen@tamarindridgeline.biz</li>
      <li><svg class="icon" viewBox="0 0 16 16" aria-hidden="true"><circle cx="8" cy="8" r="7"/></svg>www.tamarindridgeline.biz</li>
    </ul>

    <svg class="front-band" viewBox="0 0 620 60" preserveAspectRatio="none" aria-hidden="true">
      <path d="M0 46 L420 46 L440 34 L620 34 L620 60 L0 60 Z" fill="#1f72bd"/>
      <path d="M440 48 L620 40 L620 60 L420 60 Z" fill="#2b2b2b"/>
    </svg>
  </section>

</main>
</body>
</html>
```